Doctor business card, bold, modern, stand out, keep worthy

I'm a specialist doctor (Oncology and hematology) and I need a flashy business card to hand out to other doctors. I am looking for something that stands out, either with embossing or transparency or high quality paper. I want my card not to look or feel generic. I'm a hematology oncology specialist, and somewhere on the card I should incorporate the TLVB logo, along with my name, my title (hematology/oncology) and board certifications (in oncology and internal medicine), finally with our practice address (82 Orchard Ave Suite 4 Edison NJ 08815) and tel and fax numbers

Target Market(s)

other doctors, patients

Industry/Entity Type

Healthcare

Contact Information for Business Card

1. my name 2. Job title (hematology/Oncology) 3. credentials (Board Certified Medical Oncology/Board Certified Internal Medicine) 4. Address 5. Phone and Fax Number

Font styles to use
Serif

Colors

Designer to choose colors to be used in the design.

Requirements
Nice to have
• flip side can have logo and date of appt blank line. Blue green colors but can vary

```html
<!DOCTYPE html>
<html lang="en">
<head>
<meta charset="utf-8">
<title>TLVB – Maren Dubrava Business Card</title>
<link rel="stylesheet" href="https://fonts.googleapis.com/css2?family=Open+Sans:wght@400;700&display=swap">
<style>
  :root {
    --page: #2b2b2e;
    --card-dark: #1f1e23;
    --cyan: #1cb9e3;
    --cyan-deep: #1497bd;
    --purple: #9b4a8c;
    --purple-deep: #5b3566;
    --leaf-pale: #bfe3ef;
    --white: #ffffff;
    --text-light: #f2f2f4;
  }
  * { box-sizing: border-box; margin: 0; padding: 0; }
  html, body { width: 1200px; height: 780px; overflow: hidden; }
  body {
    background: var(--page);
    font-family: "Open Sans", Arial, sans-serif;
    position: relative;
  }
  .card {
    position: absolute;
    top: 240px;
    width: 520px;
    height: 300px;
    overflow: hidden;
  }
  .card-front { left: 60px; background: var(--card-dark); }
  .card-back { left: 620px; background: var(--cyan); }

  .front-art { position: absolute; inset: 0; }

  .leaf-illustration {
    position: absolute;
    left: 80px; top: 28px;
    width: 190px; height: 120px;
    border-radius: 60% 40% 55% 45%;
    background: linear-gradient(135deg, var(--leaf-pale) 0%, var(--cyan) 35%, var(--purple) 70%, var(--purple-deep) 100%);
    opacity: .9;
  }

  .divider {
    position: absolute;
    left: 238px; top: 70px;
    width: 2px; height: 190px;
    background: linear-gradient(to bottom, rgba(255,255,255,0.2), var(--white));
  }

  .details {
    position: absolute;
    left: 256px; top: 70px;
    color: var(--text-light);
  }
  .doctor-name { font-size: 30px; font-weight: 700; line-height: 1.05; letter-spacing: .5px; }
  .doctor-name .first { color: var(--cyan); }
  .doctor-name .last { color: var(--purple); }
  .specialty { font-size: 15px; margin-top: 6px; }
  .address { font-size: 13px; line-height: 1.35; margin-top: 10px; }
  .contact-list { list-style: none; margin-top: 10px; font-size: 13px; line-height: 1.45; }
  .contact-list li { display: flex; align-items: center; gap: 8px; }
  .contact-list svg { width: 12px; height: 12px; flex: none; }

  .practice-name {
    position: absolute;
    left: 26px; top: 22px;
    color: var(--white);
    font-size: 28px;
    font-weight: 400;
    letter-spacing: 3px;
  }
  .leaf-pattern {
    position: absolute;
    left: 0; top: 0; width: 100%; height: 100%;
    background: linear-gradient(120deg, var(--cyan-deep) 0%, var(--cyan) 55%, #6fd3ee 100%);
    opacity: .55;
  }
  .credentials {
    position: absolute;
    left: 26px; bottom: 22px;
    color: var(--white);
    font-size: 13.5px;
  }
</style>
</head>
<body>

<section class="card card-front" aria-label="Business card front">
  <svg class="front-art" viewBox="0 0 520 300" aria-hidden="true">
    <path d="M0 110 C 70 150, 150 250, 330 300 L 0 300 Z" fill="var(--purple)"/>
    <path d="M95 200 C 150 250, 230 285, 330 300 L 318 300 C 220 282, 145 248, 95 200 Z" fill="var(--cyan)"/>
  </svg>
  <div class="leaf-illustration" role="img" aria-label="Fan of overlapping translucent leaves in pale blue, cyan and purple"></div>
  <div class="divider"></div>

  <div class="details">
    <h1 class="doctor-name"><span class="first">Maren</span> <span class="last">Dubrava</span></h1>
    <p class="specialty">Hematology/Oncology</p>
    <p class="address">82 Orchard Ave Suite 4 Edison<br>NJ 08815</p>
    <ul class="contact-list">
      <li>
        <svg viewBox="0 0 24 24"><path fill="var(--cyan)" d="M6.6 10.8a15 15 0 0 0 6.6 6.6l2.2-2.2a1 1 0 0 1 1-.25 11.4 11.4 0 0 0 3.6.6 1 1 0 0 1 1 1V20a1 1 0 0 1-1 1A17 17 0 0 1 3 4a1 1 0 0 1 1-1h3.5a1 1 0 0 1 1 1 11.4 11.4 0 0 0 .6 3.6 1 1 0 0 1-.25 1z"/></svg>
        (555) 014-2290
      </li>
      <li>
        <svg viewBox="0 0 24 24"><rect x="3" y="9" width="18" height="12" rx="2" fill="var(--cyan)"/><rect x="7" y="3" width="10" height="7" fill="var(--cyan)"/></svg>
        (555) 014-2291
      </li>
      <li>
        <svg viewBox="0 0 24 24"><rect x="2" y="5" width="20" height="14" rx="2" fill="var(--cyan)"/><path d="M2 6l10 7 10-7" stroke="var(--card-dark)" stroke-width="2" fill="none"/></svg>
        info@tlvbcancercare.org
      </li>
      <li>
        <svg viewBox="0 0 24 24"><circle cx="12" cy="12" r="10" fill="var(--cyan)"/><path d="M2 12h20M12 2c3 3 3 17 0 20M12 2c-3 3-3 17 0 20" stroke="var(--card-dark)" stroke-width="1.5" fill="none"/></svg>
        www.tlvbcancercare.org
      </li>
    </ul>
  </div>
</section>

<section class="card card-back" aria-label="Business card back">
  <div class="leaf-pattern" role="img" aria-label="Repeating pattern of small leaf motifs in darker and lighter cyan"></div>
  <p class="practice-name">TLVB</p>
  <p class="credentials">Board Certified Medical Oncology/Board Certified Internal Medicine</p>
</section>

</body>
</html>
```